Create a proposal + product powerpoint

Please see the powerpoint for the slides. There are about 20 slides to be created. Rest of them are for reference and show the design that I like.

I would like to move fast on this, since I need to present it next week (in the week of April 21st).

Please download the current content from here:
https://www.parcelbrook.net/fetch/qRtVmXzLwPkNbYcD

Please make at least 4 slides with the specific content so I can assess your design style.

Target Market(s)

Business Audience and very senior technical audience
Decision Makers

Industry/Entity Type

Product

Colors
e34297
a64599

Requirements
Must have
• Should be very clean, crisp.

I like to use Icons as shown in the powerpoint.... Please see the appendix of the slide deck that shows the various icons. Most of them just have plain text, and I would like to organize so that it does not look like some is just reading text.

I would like to focus on the design aspects so that the audience is clear on how the solution works.

Every page should some graphic element based on the slides shown in the appendix.

```html
<!DOCTYPE html>
<html lang="en">
<head>
<meta charset="utf-8">
<title>Approach</title>
<link rel="stylesheet" href="https://fonts.googleapis.com/css2?family=Archivo+Narrow:wght@400;500;600&family=Saira+Semi+Condensed:wght@400;600&display=swap">
<style>
  :root {
    --header-band: #f0c6ef;
    --header-rule: #d79ad8;
    --haze: #f9e3f6;
    --title-ink: #2e2a2e;
    --logo-ink: #8d8d8d;
    --card-border: #b35fc2;
    --card-head: #d96ad7;
    --bullet: #a3409c;
    --body-ink: #2c2c2c;
    --footer-dark: #9c1f5c;
    --footer-light: #a64599;
    --white: #ffffff;
  }
  * { box-sizing: border-box; margin: 0; padding: 0; }
  html, body { width: 1200px; height: 900px; overflow: hidden; background: var(--white); }
  .slide {
    position: relative; width: 1200px; height: 900px; overflow: hidden;
    font-family: "Saira Semi Condensed", "Archivo Narrow", "Arial Narrow", sans-serif;
    background: var(--white);
  }
  .slide-header {
    position: absolute; left: 0; top: 0; width: 1200px; height: 96px;
    background: var(--header-band); border-bottom: 3px solid var(--header-rule);
  }
  .slide-title {
    position: absolute; left: 40px; top: 16px;
    font-family: "Archivo Narrow", "Arial Narrow", sans-serif;
    font-weight: 400; font-size: 46px; letter-spacing: -0.5px; color: var(--title-ink);
  }
  .logo-slot {
    position: absolute; left: 1035px; top: 11px; width: 150px; height: 70px;
    background: var(--white); border-radius: 10px;
    display: flex; align-items: center; justify-content: center;
    font-size: 27px; letter-spacing: 1px; color: var(--logo-ink); white-space: nowrap;
  }
  .haze {
    position: absolute; left: 0; top: 96px; width: 1200px; height: 200px;
    background: linear-gradient(180deg, var(--haze) 0%, rgba(249,227,246,0.6) 45%, rgba(255,255,255,0) 100%);
  }
  .card {
    position: absolute; top: 236px; width: 303px; height: 393px;
    border: 1.5px solid var(--card-border); background: var(--white); overflow: hidden;
  }
  .card--one { left: 97px; }
  .card--two { left: 442px; }
  .card--three { left: 786px; }
  .card-head {
    height: 51px; background: var(--card-head); color: var(--white);
    font-weight: 600; font-size: 35px; line-height: 51px; text-align: center;
  }
  .point-list { list-style: none; padding: 20px 16px 0 14px; }
  .point {
    display: flex; gap: 11px; font-size: 22px; line-height: 34px; color: var(--body-ink);
    margin-bottom: 30px;
  }
  .point:last-child { margin-bottom: 0; }
  .point svg { flex: 0 0 24px; margin-top: 5px; }
  .point-text { text-align: left; }
  .slide-footer { position: absolute; left: 0; top: 856px; width: 1200px; height: 44px; }
  .footer-shape { position: absolute; left: 0; top: 0; }
  .page-number {
    position: absolute; left: 15px; top: 0; line-height: 44px;
    font-size: 24px; color: var(--white); letter-spacing: 0.5px;
  }
  .copyright {
    position: absolute; right: 14px; top: 0; line-height: 40px;
    font-size: 24px; color: var(--white); letter-spacing: 0.5px;
  }
</style>
</head>
<body>
<main class="slide">
  <header class="slide-header">
    <h1 class="slide-title">Approach</h1>
    <div class="logo-slot">LOGO HERE</div>
  </header>
  <div class="haze"></div>

  <section class="card card--one">
    <h2 class="card-head">People</h2>
    <ul class="point-list">
      <li class="point"><svg width="24" height="24" viewBox="0 0 24 24"><circle cx="12" cy="12" r="12" fill="var(--bullet)"/><path d="M9.5 6.5 L15 12 L9.5 17.5" fill="none" stroke="#fff" stroke-width="3" stroke-linecap="round" stroke-linejoin="round"/></svg><span class="point-text">Work with experienced Cloudwright product development organizations</span></li>
      <li class="point"><svg width="24" height="24" viewBox="0 0 24 24"><circle cx="12" cy="12" r="12" fill="var(--bullet)"/><path d="M9.5 6.5 L15 12 L9.5 17.5" fill="none" stroke="#fff" stroke-width="3" stroke-linecap="round" stroke-linejoin="round"/></svg><span class="point-text">Engage Cloudwright MVPs</span></li>
      <li class="point"><svg width="24" height="24" viewBox="0 0 24 24"><circle cx="12" cy="12" r="12" fill="var(--bullet)"/><path d="M9.5 6.5 L15 12 L9.5 17.5" fill="none" stroke="#fff" stroke-width="3" stroke-linecap="round" stroke-linejoin="round"/></svg><span class="point-text">Review with Cloudwright Product Managers</span></li>
    </ul>
  </section>

  <section class="card card--two">
    <h2 class="card-head">People</h2>
    <ul class="point-list">
      <li class="point"><svg width="24" height="24" viewBox="0 0 24 24"><circle cx="12" cy="12" r="12" fill="var(--bullet)"/><path d="M9.5 6.5 L15 12 L9.5 17.5" fill="none" stroke="#fff" stroke-width="3" stroke-linecap="round" stroke-linejoin="round"/></svg><span class="point-text">Work with experienced Cloudwright product development organizations</span></li>
      <li class="point"><svg width="24" height="24" viewBox="0 0 24 24"><circle cx="12" cy="12" r="12" fill="var(--bullet)"/><path d="M9.5 6.5 L15 12 L9.5 17.5" fill="none" stroke="#fff" stroke-width="3" stroke-linecap="round" stroke-linejoin="round"/></svg><span class="point-text">Engage Cloudwright MVPs</span></li>
      <li class="point"><svg width="24" height="24" viewBox="0 0 24 24"><circle cx="12" cy="12" r="12" fill="var(--bullet)"/><path d="M9.5 6.5 L15 12 L9.5 17.5" fill="none" stroke="#fff" stroke-width="3" stroke-linecap="round" stroke-linejoin="round"/></svg><span class="point-text">Review with Cloudwright Product Managers</span></li>
    </ul>
  </section>

  <section class="card card--three">
    <h2 class="card-head">People</h2>
    <ul class="point-list">
      <li class="point"><svg width="24" height="24" viewBox="0 0 24 24"><circle cx="12" cy="12" r="12" fill="var(--bullet)"/><path d="M9.5 6.5 L15 12 L9.5 17.5" fill="none" stroke="#fff" stroke-width="3" stroke-linecap="round" stroke-linejoin="round"/></svg><span class="point-text">Work with experienced Cloudwright product development organizations</span></li>
      <li class="point"><svg width="24" height="24" viewBox="0 0 24 24"><circle cx="12" cy="12" r="12" fill="var(--bullet)"/><path d="M9.5 6.5 L15 12 L9.5 17.5" fill="none" stroke="#fff" stroke-width="3" stroke-linecap="round" stroke-linejoin="round"/></svg><span class="point-text">Engage Cloudwright MVPs</span></li>
      <li class="point"><svg width="24" height="24" viewBox="0 0 24 24"><circle cx="12" cy="12" r="12" fill="var(--bullet)"/><path d="M9.5 6.5 L15 12 L9.5 17.5" fill="none" stroke="#fff" stroke-width="3" stroke-linecap="round" stroke-linejoin="round"/></svg><span class="point-text">Review with Cloudwright Product Managers</span></li>
    </ul>
  </section>

  <footer class="slide-footer">
    <svg class="footer-shape" width="1200" height="44" viewBox="0 0 1200 44">
      <polygon points="0,0 905,0 925,44 0,44" fill="var(--footer-dark)"/>
      <polygon points="920,0 1200,0 1200,44 940,44" fill="var(--footer-light)"/>
    </svg>
    <span class="page-number">Page : 01</span>
    <span class="copyright">Copyright text here</span>
  </footer>
</main>
</body>
</html>
```